Webdesign für Brenner Werkstatt
Zielgruppe
Brenner Werkstatt produziert GfK Formteile und Abdeckungen
Einzelanfertigungen • Negativ - Formenbau • Prototyping • Ur-Modellbau
Formteile • Abdeckungen • Behälter • Sonderanfertigungen • Beschichtungen
Prototypen Modellbau • Anfertigung von Negativformen • Reparaturen • Fahrzeugteile
Hauptzielgruppe ist die Luftfahrtindustrie (Abdeckungen für Triebwerke)
Durch den Prototypenbau und die Einzelanfertigungen ist die Zielgruppe nicht klar zu definieren. Es werden Einzelteile jeglicher Art aus GfK hergestellt.
Dies können auch Anbauteile für PKW, Poolbeschichtungen, Teile für Boote etc sein.
Es gibt auch Kleinserien. Beispielsweise baut Brenner-Werkstatt Motorhauben für Karl-Honstett Rasenmähertrecker aus den 70er Jahren nach, die es nicht mehr zu kaufen gibt.
Aufgabenstellung
Der Designer hat alle Freiheiten. Die Seite muss natürlich responsiv funktionieren.
Außer dem Logo gibt es keine must-haves.
Schriftart aus dem Logo: EXO 2

```html
<!DOCTYPE html>
<html lang="de">
<head>
<meta charset="utf-8">
<title>Brenner Werkstatt – GfK Formteile</title>
<link rel="stylesheet" href="https://fonts.googleapis.com/css2?family=Exo+2:wght@300;400;500;700;800&display=swap">
<style>
:root{
  --blue:#1b5d9e;
  --blue-dark:#134a82;
  --blue-light:#2a6fb2;
  --grey:#f1f1f1;
  --box:#ececec;
  --text:#222;
  --orange:#f39200;
  --orange-light:#ffb000;
  --white:#fff;
}
*{box-sizing:border-box;margin:0;padding:0}
html,body{width:1200px;height:3479px;overflow:hidden}
body{font-family:"Exo 2",sans-serif;color:var(--text);background:var(--white);position:relative}
.abs{position:absolute}

/* header */
.brand-mark{left:112px;top:30px;width:176px;height:176px;border-radius:50%;background:var(--blue);opacity:.12}
.brand-name{left:322px;top:62px;font-size:66px;font-weight:800;color:var(--blue);letter-spacing:-1px;line-height:1}
.brand-tag{left:322px;top:142px;font-size:20px;color:#555;font-weight:400}
.top-links{right:170px;top:18px;display:flex;gap:24px;font-size:15px;color:var(--blue)}
.flag{left:1056px;top:16px;width:34px;height:22px}

.mainnav{left:0;top:180px;width:1200px;height:51px;background:var(--blue)}
.mainnav a{position:absolute;top:0;height:51px;line-height:51px;color:var(--white);font-size:17px;text-decoration:none;text-align:center}
.mainnav .active{background:var(--blue-dark)}

/* hero */
.hero{left:0;top:231px;width:1200px;height:492px;background:linear-gradient(180deg,#b8c7d4 0%,#dfe6ec 45%,#9ea6ad 75%,#7f858b 100%)}
.dropdown{left:534px;top:231px;width:259px;background:rgba(255,255,255,.93);list-style:none}
.dropdown li{height:39px;line-height:39px;text-align:center;font-size:14.5px;color:var(--blue);border-bottom:1px solid #c9d4df}
.hero-claim{left:808px;top:266px;width:392px;height:112px;background:rgba(255,255,255,.88);padding:20px 0 0 33px;font-size:30px;font-weight:700;color:var(--blue);line-height:36px}
.slide-btn{top:453px;width:62px;height:60px;background:rgba(255,255,255,.75)}
.slide-btn svg{position:absolute;left:19px;top:18px}

/* about */
.section-title{width:1200px;left:0;text-align:center;font-size:29px;font-weight:700;color:var(--blue)}
.about-photo{left:109px;top:839px;width:452px;height:331px;background:linear-gradient(135deg,#2c5fb0,#5a86c8 55%,#c9ccd0)}
.about-text{left:109px;top:1187px;width:460px;font-size:19.5px;line-height:24px}
.info-box{left:643px;width:449px;background:var(--box)}
.info-box h3{position:absolute;left:91px;font-size:30px;font-weight:400;color:var(--blue-light)}
.info-box svg{position:absolute;left:10px}
.info-box p{font-size:19.5px;line-height:24px;margin-bottom:24px}

/* products */
.products-bg{left:0;top:1578px;width:1200px;height:1443px;background:var(--grey)}
.view-icons{left:1007px;top:1648px}
.card{width:289px;height:503px;background:var(--white);box-shadow:0 2px 8px rgba(0,0,0,.12);text-align:center}
.card .pic{position:absolute;left:12px;top:12px;width:265px;height:262px}
.card h4{position:absolute;left:0;top:298px;width:100%;font-size:19px;font-weight:800;color:var(--blue);line-height:24px}
.card p{position:absolute;left:10px;top:354px;width:269px;font-size:16.5px;line-height:21px}
.card .btn{position:absolute;left:93px;top:447px;width:103px;height:31px;line-height:31px;color:var(--white);font-weight:700;font-size:16px;background:linear-gradient(180deg,var(--orange-light),var(--orange));box-shadow:0 2px 6px rgba(0,0,0,.2)}

/* contact */
.contact-tab{left:89px;top:2976px;width:204px;height:46px;background:var(--blue);clip-path:polygon(20px 0,100% 0,100% 100%,0 100%)}
.contact-tab span{position:absolute;left:50px;top:5px;color:var(--white);font-size:29px;font-weight:700}
.contact{left:0;top:3021px;width:1200px;height:458px;background:var(--blue);color:var(--white)}
.contact .co-name{position:absolute;left:138px;top:40px;font-size:28px;font-weight:700}
.contact address{position:absolute;left:138px;top:97px;font-style:normal;font-size:19.5px;font-weight:500;line-height:24px}
.contact .phones{position:absolute;left:138px;top:194px;font-size:19.5px;font-weight:500;line-height:24px}
.contact .phones b{display:inline-block;width:60px;font-weight:500}
.contact h3{position:absolute;left:662px;top:42px;font-size:28px;font-weight:700}
.field{position:absolute;left:642px;width:447px;background:var(--white);border:2px solid #cfd8e3;color:var(--blue);font-size:19px;padding:8px 19px}
.send{position:absolute;left:970px;top:367px;width:119px;height:37px;background:var(--blue-dark);color:var(--white);font-weight:700;font-size:19px;text-align:center;line-height:37px}
</style>
</head>
<body>

<header>
  <div class="abs brand-mark"></div>
  <div class="abs brand-name">Brenner Werkstatt</div>
  <div class="abs brand-tag">GfK Formteile | Ur-Modellbau | Prototyping</div>
  <nav class="abs top-links"><span>Impressum</span><span>AGB</span></nav>
  <svg class="abs flag" viewBox="0 0 34 22"><rect width="34" height="6" fill="#000"/><rect y="6" width="34" height="6" fill="#d00"/><rect y="12" width="34" height="6" fill="#fc0"/><path d="M13 18h8l-4 4z" fill="#bbb"/></svg>
</header>

<nav class="abs mainnav">
  <a style="left:312px;width:96px">Startseite</a>
  <a style="left:436px;width:84px">Über uns</a>
  <a class="active" style="left:534px;width:259px">Produkte &amp; Dienstleistungen</a>
  <a style="left:808px;width:80px">Kontakt</a>
</nav>

<section>
  <div class="abs hero" role="img" aria-label="Verkehrsflugzeug mit gelbem Schlepper auf dem Vorfeld"></div>
  <ul class="abs dropdown">
    <li>Luftfahrt Formbauteile</li>
    <li>Aufblasbare Sonderabdeckungen</li>
    <li>Formbauteile</li>
    <li>Ur-Modellbau</li>
    <li>Aquarienrückwände</li>
    <li>Dekoration &amp; Kunstfelsen</li>
    <li>Fahrzeugteile</li>
    <li>Prototypen Metallbau</li>
    <li>Reparaturen</li>
  </ul>
  <div class="abs hero-claim">Abdeckungen für<br>Triebwerke</div>
  <div class="abs slide-btn" style="left:0"><svg width="22" height="24" viewBox="0 0 22 24"><path d="M15 3 6 12l9 9" fill="none" stroke="#1b5d9e" stroke-width="4"/></svg></div>
  <div class="abs slide-btn" style="left:1138px"><svg width="22" height="24" viewBox="0 0 22 24"><path d="M7 3l9 9-9 9" fill="none" stroke="#1b5d9e" stroke-width="4"/></svg></div>
</section>

<section>
  <h2 class="abs section-title" style="top:758px">Über uns</h2>
  <div class="abs about-photo" role="img" aria-label="Triebwerk unter blauer Schutzabdeckung auf Transportgestell"></div>
  <p class="abs about-text">Wir entwickeln und fertigen geometrisch an­spruchsvolle Formteile von höchster Qualität. Die von uns konzipierten Verbundwerkstoffe mit ihren herausragenden Oberflächen- und Materialeigen­schaften bieten konstruktive Vorteile und erweit­ern die gestalterischen Möglichkeiten.</p>

  <div class="abs info-box" style="top:838px;height:546px">
    <svg style="top:8px" width="66" height="50" viewBox="0 0 66 50"><path d="M2 10l14-6 10 6 8-4 10 2 20-4 10 6-6 24-12 12-8-4-8 6-10-6-12-10L2 26z" fill="#1b5d9e"/><path d="M20 22l10 8M26 16l14 12" stroke="#fff" stroke-width="3"/></svg>
    <h3 style="top:10px">Kundenorientiert</h3>
    <div style="position:absolute;left:22px;top:78px;width:410px">
      <p>Die intensive, vertrauensvolle Zusammenar­beit mit unseren Kunden ist für uns eine der wichtigsten Voraussetzungen für den ge­meinsamen Erfolg. Wir bieten darum bereits im Vorfeld eines Projekts umfassende Bera­tung und zeigen das breit gefächerte An­wendungsspektrum von faserverstärkten Kunststoffen auf.</p>
      <p>In enger Kooperation mit Ihnen entwickeln wir unter Einbindung aller gestalterischen und technischen Gesichtspunkte maß­geschneiderte, individuelle Lösungen für Ihre Anforderungen und Anwendungen.</p>
      <p>Im Mittelpunkt unseres Handels steht dabei die technisch perfekte, schnelle und wirtschaftliche Umsetzung der Ideen und Entwürfe unserer Kunden.</p>
    </div>
  </div>

  <div class="abs info-box" style="top:1409px;height:60px">
    <svg style="top:8px" width="66" height="46" viewBox="0 0 66 46"><path d="M6 42A28 28 0 0 1 60 42" fill="none" stroke="#1b5d9e" stroke-width="8"/><path d="M30 40 50 20" stroke="#1b5d9e" stroke-width="5"/><circle cx="30" cy="40" r="5" fill="#1b5d9e"/></svg>
    <h3 style="top:10px">Leistungsstark</h3>
  </div>
</section>

<section>
  <div class="abs products-bg"></div>
  <h2 class="abs section-title" style="top:1636px">Produkte &amp; Dienstleistungen</h2>
  <svg class="abs view-icons" width="82" height="28" viewBox="0 0 82 28"><path d="M8 6 2 14l6 8M28 6l6 8-6 8" fill="none" stroke="#333" stroke-width="3"/><rect x="14" y="5" width="9" height="18" fill="#333"/><g fill="#1b5d9e"><rect x="56" y="5" width="7" height="6"/><rect x="65" y="5" width="7" height="6"/><rect x="74" y="5" width="7" height="6"/><rect x="56" y="13" width="7" height="6"/><rect x="65" y="13" width="7" height="6"/><rect x="74" y="13" width="7" height="6"/><rect x="56" y="21" width="7" height="6"/><rect x="65" y="21" width="7" height="6"/><rect x="74" y="21" width="7" height="6"/></g></svg>

  <article class="abs card" style="left:108px;top:1724px">
    <div class="pic" role="img" aria-label="Gelbe Triebwerksabdeckung aus GfK" style="background:linear-gradient(135deg,#e6e84a,#c9cc1c 60%,#8a8f94)"></div>
    <h4>Luftfahrt Formbauteile</h4>
    <p>Anfertigung von Triebwerkcover für jeden Triebwerktypen.</p>
    <div class="btn">Details</div>
  </article>
  <article class="abs card" style="left:454px;top:1724px">
    <div class="pic" role="img" aria-label="Aufblasbare Sonderabdeckung in einer Halle" style="background:radial-gradient(circle at 55% 55%,#eef0f2,#c4c8cc 60%,#8d9196)"></div>
    <h4 style="top:287px">Aufblasbare<br>Sonderabdeckungen</h4>
    <p>Anfertigung von Triebwerkcover für jeden Triebwerktypen.</p>
    <div class="btn">Details</div>
  </article>
  <article class="abs card" style="left:800px;top:1724px">
    <div class="pic" role="img" aria-label="Blaue technische Formbauteile mit gelben Ringen" style="background:linear-gradient(135deg,#2d63c4,#1f4fa8 60%,#c7b24a)"></div>
    <h4>Formbauteile</h4>
    <p>Anfertigung von technischen Formbauteilen (Einzelstück oder Kleinserien).</p>
    <div class="btn">Details</div>
  </article>

  <article class="abs card" style="left:108px;top:2286px">
    <div class="pic" role="img" aria-label="Aquarienrückwand mit Felsstruktur und Sandboden" style="background:linear-gradient(180deg,#4a4c4a,#6a6a66 60%,#e8e6e2)"></div>
    <h4>Aquarium Rückwände</h4>
    <p>3D - Kunstfelsenrückwand mit echter Granitkies-Oberfläche</p>
    <div class="btn">Details</div>
  </article>
  <article class="abs card" style="left:454px;top:2286px">
    <div class="pic" role="img" aria-label="Dekorative Kunstfelsen-Wasserlandschaft" style="background:linear-gradient(160deg,#6d6a55,#3a62a8 50%,#2f7c4a)"></div>
    <h4>Dekoration &amp; Kunstfelsen</h4>
    <p>Anfertigung von Triebwerkcover für jeden Triebwerktypen.</p>
    <div class="btn">Details</div>
  </article>
  <article class="abs card" style="left:800px;top:2286px">
    <div class="pic" role="img" aria-label="Reparierte helle GfK-Oberfläche" style="background:linear-gradient(160deg,#d8dad8,#f2f2f0 55%,#c6c8c6)"></div>
    <h4>Reperaturservice</h4>
    <p>Anfertigung von technischen Formbauteilen (Einzelstück oder Kleinserien).</p>
    <div class="btn">Details</div>
  </article>
</section>

<footer>
  <div class="abs contact-tab"><span>Kontakt</span></div>
  <div class="abs contact">
    <div class="co-name">Brenner Werkstatt</div>
    <address>Geschäftsführer: M. Lindner<br>Ahornweg 14<br>31234 Feldhausen</address>
    <div class="phones"><b>Tel.</b>+49 123 / 456 78 90<br><b>Fax.</b>+49 123 / 456 78 91</div>
    <h3>Ihre Nachricht</h3>
    <div class="field" style="top:85px;height:43px">Name</div>
    <div class="field" style="top:146px;height:43px">E-Mail</div>
    <div class="field" style="top:208px;height:143px">Nachricht</div>
    <div class="send">SENDEN</div>
  </div>
</footer>

</body>
</html>
```